Venture Capital Investment Firm

We are looking to overhaul our existing website (substantially), with only using the same logos (which we can provide).
We are an investment firm that focuses on making loans to late stage technology companies. Our site should ultimately look like other venture capital firms, and look modern and fresh. We have an existing website www.norvellhub.com which this will be replacing, although we will be using a lot of the existing written content, and potentially the numbers of pages we will need, we are not wed to anything else. Please feel free to shoot any questions at any time and thank you in advance for your help!
Websites we like as examples:
https://www.tesmarkfund.com/
https://www.brindlewoodpartners.com/
Target Market(s)
Potential investors who will invest in our firm, as well as potentially companies that are looking to borrow money from us.
Coding
Coded - Design and coding required
Number of Pages Required
5+ page
Colors
Designer to choose colors to be used in the design.
Look and feel

```html
<!DOCTYPE html>
<html lang="en">
<head>
<meta charset="utf-8">
<title>Contact Us — Norvell Hub</title>
<link rel="stylesheet" href="https://fonts.googleapis.com/css2?family=Raleway:wght@300;400;500&display=swap">
<style>
:root{
  --navy:#14234a;
  --teal:#1d5a78;
  --link:#2f86a8;
  --gold:#e8d6a4;
  --ink:#1c2433;
  --panel:#eaecef;
  --footer:#173a4e;
  --white:#ffffff;
}
*{box-sizing:border-box;margin:0;padding:0}
html,body{width:1200px;height:2258px;overflow:hidden;background:var(--white)}
body{font-family:"Raleway",sans-serif;color:var(--ink);position:relative}
.hero{position:absolute;left:0;top:0;width:1200px;height:548px;
  background:linear-gradient(180deg,#3f8fb0 0%,#8fbdd2 22%,#dfe9f0 48%,#e9eef2 64%,#c3c8c9 72%,#6d7a80 80%,#3b4a52 90%,#2a3940 100%)}
.site-header{position:absolute;left:150px;top:21px;width:899px;height:41px;display:flex;align-items:center}
.brand{display:flex;align-items:center;gap:10px;font-size:22px;font-weight:500;color:var(--navy);letter-spacing:.5px}
.brand-dot{width:22px;height:22px;border-radius:50%;background:var(--navy)}
.main-nav{position:absolute;left:0;top:0;width:100%;height:100%}
.main-nav a{position:absolute;top:14px;font-size:11px;letter-spacing:.6px;color:#3d4f66;text-decoration:none;font-weight:400}
.main-nav a.current{text-decoration:underline}
.login{position:absolute;left:756px;top:0;width:143px;height:41px;border:1px solid var(--navy);border-radius:21px;
  font-size:11px;letter-spacing:.6px;color:var(--navy);display:flex;align-items:center;justify-content:center}
.hero-title{position:absolute;top:214px;width:1200px;text-align:center;font-size:42px;font-weight:400;color:var(--navy)}
.hero-intro{position:absolute;top:274px;width:1200px;text-align:center;font-size:16px;line-height:24px;font-weight:300;color:#2d3443}
.divider{position:absolute;left:600px;top:513px;width:1px;height:76px;background:var(--link)}
.contacts{position:absolute;left:150px;top:655px;width:899px;height:409px;
  background:linear-gradient(120deg,#eef0f3 0%,#e6e9ed 50%,#e4e7eb 100%);text-align:center}
.contact-item{position:absolute;left:0;width:100%}
.contact-item h3{font-size:16px;font-weight:500;color:var(--ink);letter-spacing:.4px;line-height:20px}
.contact-item a{display:block;margin-top:7px;font-size:16px;font-weight:400;color:var(--link);text-decoration:none;line-height:20px}
.office{position:absolute;top:1142px;width:1200px;text-align:center}
.office h2{font-size:30px;font-weight:500;color:var(--teal)}
.office .rule{width:52px;height:2px;background:var(--gold);margin:12px auto 0}
.office address{font-style:normal;margin-top:22px;font-size:16px;line-height:27px;color:var(--teal)}
.map{position:absolute;left:151px;top:1328px;width:898px;height:398px;
  background:linear-gradient(90deg,#7a7a7a 0%,#7a7a7a 36%,#dadada 44%,#cfcfcf 58%,#7a7a7a 64%,#8a8a8a 74%,#dedede 84%,#e8e8e8 100%)}
.map-strip{position:absolute;left:151px;top:1726px;width:898px;height:14px;background:#f5f6f7}
.site-footer{position:absolute;left:0;top:1914px;width:1200px;height:344px;
  background:linear-gradient(180deg,#143246 0%,#1b4055 55%,#27485a 80%,#1a3646 100%)}
.footer-brand{position:absolute;top:110px;width:100%;display:flex;justify-content:center;align-items:center;gap:14px;
  font-size:40px;font-weight:500;color:var(--white)}
.footer-brand .brand-dot{width:40px;height:40px;background:var(--white)}
.footer-nav a{position:absolute;top:206px;font-size:11px;letter-spacing:.6px;color:#dfe7ec;text-decoration:none}
.legal{position:absolute;top:307px;width:100%;text-align:center;font-size:7px;line-height:12px;color:#dfe7ec}
.legal a{color:#dfe7ec}
</style>
</head>
<body>
<div class="hero" role="img" aria-label="Aerial photograph of a city skyline at sunrise beneath a pale blue sky"></div>
<header class="site-header">
  <div class="brand"><span class="brand-dot"></span>Norvell Hub</div>
  <nav class="main-nav">
    <a style="left:276px">STRATEGY</a>
    <a style="left:387px">ABOUT US</a>
    <a style="left:487px">TEAM</a>
    <a style="left:575px">NEWS</a>
    <a class="current" style="left:674px">CONTACT</a>
    <span class="login">INVESTORS LOGIN</span>
  </nav>
</header>
<h1 class="hero-title">Contact Us</h1>
<p class="hero-intro">For any inquiries, feel free to contact us through these<br>contacts respectivelly</p>
<div class="divider"></div>

<section class="contacts" role="img" aria-label="Faded photograph of a person in a suit holding a coffee cup, behind the contact list">
  <div class="contact-item" style="top:61px"><h3>General Inquiries</h3><a>inquiries@norvellhub.com</a></div>
  <div class="contact-item" style="top:142px"><h3>Transaction Opportunities</h3><a>invopps@norvellhub.com</a></div>
  <div class="contact-item" style="top:223px"><h3>Media Inquiries</h3><a>media@norvellhub.com</a></div>
  <div class="contact-item" style="top:304px"><h3>Careers</h3><a>career@norvellhub.com</a></div>
</section>

<section class="office">
  <h2>San Francisco</h2>
  <div class="rule"></div>
  <address>2140 Halvern Street #310<br>San Francisco, CA 94107</address>
</section>
<div class="map" role="img" aria-label="Greyscale map of the San Francisco Bay Area with the office location pinned"></div>
<div class="map-strip"></div>

<footer class="site-footer" role="img" aria-label="Dark teal photograph of a suspension bridge over the bay">
  <div class="footer-brand"><span class="brand-dot"></span>NorvellHub</div>
  <nav class="footer-nav">
    <a style="left:361px">STRATEGY</a>
    <a style="left:478px">ABOUT US</a>
    <a style="left:596px">TEAM</a>
    <a style="left:687px">NEWS</a>
    <a style="left:781px">CONTACT</a>
  </nav>
  <p class="legal">Norvell Hub &nbsp;•&nbsp; San Francisco<br>© 2020 Norvell Hub Investment Partners LLC. All Rights Reserved &nbsp;|&nbsp; <a>Legal Disclaimer</a></p>
</footer>
</body>
</html>
```